Verodex business card

Business card for sustainable investment company called "Verodex". Verodex is an exchange platform selling carbon credits between buyers and sellers. Carbon Credits are an environmental commodity for reducing global carbon emissions.

the card should obviously have our logo and the theme should be sustainability/environment mixed with a trading platform.

Contact Information for Business Card

Logo, Name, Title, Phone, Email

Colors
0054AA
0677BA
7BADD7
CADEEF
E8F1F8
0094D4
00A9DD
6FCCEA
C7EBF8
E9F6FB
00AB8E
00BBA5
67D7C9
C6EFE9
E9F9F6
59FF00
82FF00
B8FF75
E3FFCB
F4FFEA

```html
<!DOCTYPE html>
<html lang="en">
<head>
<meta charset="utf-8">
<title>Verodex Business Card</title>
<link href="https://fonts.googleapis.com/css2?family=Montserrat:wght@400;500;600;700&display=swap" rel="stylesheet">
<style>
  :root {
    --page-bg: #dcdcdc;
    --card-bg: #fbfbfb;
    --card-back-bg: #f0f0f0;
    --navy: #1f3350;
    --slate: #3c4a66;
    --teal: #6fcce0;
    --blue: #4c7fc4;
    --rule-top: #6fc3da;
    --rule-bottom: #3f6fb8;
  }
  * { box-sizing: border-box; margin: 0; padding: 0; }
  html, body {
    width: 1200px;
    height: 1200px;
    overflow: hidden;
    background: var(--page-bg);
    font-family: "Montserrat", sans-serif;
  }
  .canvas {
    width: 1200px;
    height: 1200px;
    display: flex;
    flex-direction: column;
    align-items: center;
    justify-content: center;
    gap: 60px;
  }
  .card {
    width: 840px;
    height: 480px;
    border-radius: 28px;
    box-shadow: 0 4px 14px rgba(0,0,0,0.12);
    position: relative;
  }
  .card-front {
    background: var(--card-bg);
    display: flex;
    align-items: center;
    justify-content: center;
  }
  .wordmark {
    display: flex;
    align-items: center;
    gap: 22px;
  }
  .wordmark-square {
    width: 54px;
    height: 54px;
    background: var(--blue);
    border-radius: 6px;
  }
  .wordmark-name {
    font-size: 76px;
    font-weight: 600;
    letter-spacing: 2px;
    color: var(--navy);
  }
  .card-back {
    background: var(--card-back-bg);
  }
  .corner-mark {
    position: absolute;
    top: 34px;
    right: 44px;
    font-size: 20px;
    font-weight: 600;
    letter-spacing: 1px;
    color: var(--blue);
  }
  .holder {
    position: absolute;
    left: 130px;
    top: 205px;
    text-align: center;
  }
  .holder-name {
    font-size: 38px;
    font-weight: 700;
    background: linear-gradient(90deg, var(--teal), var(--blue));
    -webkit-background-clip: text;
    background-clip: text;
    color: transparent;
  }
  .holder-title {
    font-size: 21px;
    font-weight: 500;
    color: var(--slate);
    margin-top: 2px;
  }
  .divider {
    position: absolute;
    left: 420px;
    top: 165px;
    width: 2px;
    height: 160px;
    background: linear-gradient(var(--rule-top), var(--rule-bottom));
  }
  .contact {
    position: absolute;
    left: 450px;
    top: 160px;
    color: var(--navy);
    font-size: 19px;
    line-height: 1.35;
  }
  .office-name { font-weight: 700; }
  .office-address { font-weight: 500; margin-bottom: 10px; }
  .contact-row {
    display: flex;
    align-items: center;
    gap: 10px;
    font-weight: 500;
    padding-left: 14px;
  }
  .contact-row svg { width: 16px; height: 16px; flex: none; }
</style>
</head>
<body>
<main class="canvas">
  <section class="card card-front">
    <div class="wordmark">
      <span class="wordmark-square"></span>
      <span class="wordmark-name">VERODEX</span>
    </div>
  </section>

  <section class="card card-back">
    <div class="corner-mark">VERODEX</div>

    <div class="holder">
      <div class="holder-name">Mark Halden</div>
      <div class="holder-title">Sales Representative</div>
    </div>

    <div class="divider"></div>

    <div class="contact">
      <div class="office-name">Verodex Head Office</div>
      <div class="office-address">Budapest XIII. Teleki utca 14.</div>
      <div class="contact-row">
        <svg viewBox="0 0 16 16" aria-hidden="true"><path d="M3 1.5l2.5 0 1.2 3-1.6 1.2a8 8 0 0 0 5.2 5.2l1.2-1.6 3 1.2v2.5a1.5 1.5 0 0 1-1.6 1.5A12.5 12.5 0 0 1 1.5 3.1 1.5 1.5 0 0 1 3 1.5z" fill="#4c7fc4"/></svg>
        <span>+36 30 555 0142</span>
      </div>
      <div class="contact-row">
        <svg viewBox="0 0 16 16" aria-hidden="true"><rect x="1" y="3" width="14" height="10" rx="1" fill="#4c7fc4"/><path d="M1.5 3.8 8 9l6.5-5.2" fill="none" stroke="#f0f0f0" stroke-width="1.3"/></svg>
        <span>szerviz@verodex.com</span>
      </div>
      <div class="contact-row">
        <svg viewBox="0 0 16 16" aria-hidden="true"><circle cx="8" cy="8" r="6.5" fill="#4c7fc4"/><path d="M1.5 8h13M8 1.5c-2.6 3-2.6 10 0 13M8 1.5c2.6 3 2.6 10 0 13" fill="none" stroke="#f0f0f0" stroke-width="1"/></svg>
        <span>www.verodex.com</span>
      </div>
    </div>
  </section>
</main>
</body>
</html>
```